Design Startseite Kanzlei-Homepage
Zielgruppe
Wir sind eine Rechtsanwaltskanzlei in Kempten (Allgäu) und regional sowie überregional in verschiedenen Rechtsgebieten tätig. Unsere Zielgruppe sind sowohl private als auch gewerbliche Mandanten.
Aufgabenstellung
Die bestehende Gestaltung wirkt derzeit aus unserer Sicht überholt. Insbesondere soll das bislang dominierende Rot vollständig entfallen.
Stattdessen stellen wir uns ein modernes, hochwertiges Erscheinungsbild vor, primär in dunklen Farbtönen (Anthrazit/Schwarz) kombiniert mit Beige- bzw. warmen Naturtönen. Ziel ist eine klare visuelle Anlehnung an unsere Kanzleiräumlichkeiten (siehe Fotos).
Die Webseite soll insgesamt moderner, klarer und visuell anspruchsvoller wirken, ohne an Seriosität und Zugänglichkeit einzubüßen. Die Balance zwischen hochwertigem Erscheinungsbild und mandantenorientierter Nutzerführung steht für uns im Vordergrund.

```html
<!DOCTYPE html>
<html lang="de">
<head>
<meta charset="utf-8">
<title>Kanzlei Meridian – Rechtsanwaltskanzlei in Kempten</title>
<link rel="stylesheet" href="https://fonts.googleapis.com/css2?family=Jost:wght@300;400;500&display=swap">
<style>
:root{
  --ink:#1b1c21;
  --ink-2:#23242a;
  --paper:#f2f0ec;
  --gold:#c39a67;
  --gold-soft:#b8925f;
  --text:#2a2a2a;
  --muted:#5d5b57;
  --muted-dark:#a9a6a0;
  --line-dark:#3b3b40;
}
*{margin:0;padding:0;box-sizing:border-box}
html,body{width:1200px;height:2400px;overflow:hidden}
body{font-family:"Jost",sans-serif;color:var(--text);background:var(--paper);position:relative}
section,header,footer{position:absolute;left:0;width:1200px}
.abs{position:absolute}
.eyebrow{font-size:12.5px;font-weight:400}
.rule{width:34px;height:2px;background:var(--gold)}
.link{font-size:13px;display:flex;align-items:center;gap:12px;font-weight:400}
.link svg{width:20px;height:10px}
.photo{position:absolute}

/* hero */
.hero{top:0;height:561px;background:var(--ink);overflow:hidden}
.hero .photo{inset:0;background:linear-gradient(100deg,#15161a 0%,#24211d 38%,#4a3b2a 55%,#6a5238 65%,#3a3530 80%,#9d9a96 100%)}
.hero .shade{position:absolute;inset:0;background:linear-gradient(90deg,rgba(15,15,18,.82) 0%,rgba(15,15,18,.35) 45%,rgba(15,15,18,0) 70%)}
.logo{color:#fff;font-weight:300;letter-spacing:3px;line-height:1}
.logo .l1{font-size:25px;display:block}
.logo .l2{font-size:15px;display:block;margin-top:5px;letter-spacing:2.5px}
.nav{position:absolute;top:40px;left:344px;display:flex;gap:32px;color:#e9e6e1;font-size:13px}
.nav-cta{position:absolute;top:29px;left:993px;width:160px;height:38px;border:1px solid var(--gold);color:#fff;font-size:13px;display:flex;align-items:center;justify-content:center}
.hero h1{position:absolute;left:61px;top:183px;color:#fff;font-weight:300;font-size:49px;line-height:54px}
.hero .lead{position:absolute;left:61px;top:372px;color:#e6e2dc;font-size:16px;line-height:26px;font-weight:300}
.btn{background:var(--gold);color:#1b1c21;font-size:15px;display:flex;align-items:center;justify-content:center;gap:18px}
.hero .btn{position:absolute;left:61px;top:457px;width:225px;height:45px}

/* about */
.about{top:561px;height:421px;background:var(--paper)}
.about .photo{left:584px;top:0;width:616px;height:421px;background:linear-gradient(120deg,#dcdad6 0%,#f3f2ef 40%,#c9c4bd 70%,#2d3440 100%)}
.about h2{font-weight:300;font-size:24px;line-height:31px;color:#1e1e1e}
.about p{font-size:12px;line-height:20px;color:var(--muted)}

/* services */
.services{top:982px;height:326px;background:var(--ink)}
.services .eyebrow{color:#e5e2dc;position:absolute;left:61px;top:40px}
.cards{position:absolute;left:61px;top:79px;display:flex}
.card{width:220px;height:200px;border-left:1px solid var(--line-dark);padding:6px 20px 0 20px;position:relative}
.card svg.ic{width:42px;height:40px}
.card h3{color:#fff;font-weight:400;font-size:15px;line-height:20px;margin-top:18px}
.card p{color:var(--muted-dark);font-size:11.5px;line-height:19px;margin-top:10px}
.card .arr{position:absolute;left:20px;bottom:10px;width:20px;height:10px}

/* team */
.team{top:1308px;height:391px;background:var(--paper)}
.team .photo{left:61px;top:86px;width:652px;height:254px;background:linear-gradient(180deg,#a9a9ab 0%,#8d8d90 40%,#2a2c33 75%,#3a3c44 100%)}
.team h2,.rooms h2{font-weight:300;font-size:25px;line-height:31px}

/* rooms */
.rooms{top:1699px;height:299px;background:var(--ink)}
.rooms .photo{left:0;top:0;width:679px;height:299px;background:linear-gradient(90deg,#d9d6d0 0%,#5a4530 25%,#8a6a45 45%,#c8c6c2 60%,#6b5236 80%,#2a2520 100%)}
.rooms h2{color:#fff}

/* testimonials */
.quotes{top:1998px;height:209px;background:var(--paper)}
.quote{position:absolute;top:84px;font-size:12.5px;line-height:20px;color:var(--text);font-weight:300}
.quote .by{margin-top:${0}px}
.stars{position:absolute;display:flex;gap:3px}
.stars svg{width:14px;height:14px;fill:var(--gold)}
.vsep{position:absolute;top:78px;width:1px;height:112px;background:#d7c6ad}

/* footer */
.contact{top:2207px;height:193px;background:var(--ink)}
.contact h2{position:absolute;left:61px;top:19px;color:#fff;font-weight:300;font-size:25px;line-height:31px}
.contact .small{color:#c9c6c0;font-size:11.5px;line-height:19px}
.contact .hr{position:absolute;left:40px;top:104px;width:1118px;height:1px;background:var(--line-dark)}
.foot{color:#d9d6d0;font-size:12px;line-height:19px}
</style>
</head>
<body>

<header class="hero">
  <div class="photo" role="img" aria-label="Empfangsbereich der Kanzlei mit beleuchtetem Holztresen und dunklen Wänden"></div>
  <div class="shade"></div>
  <div class="logo abs" style="left:47px;top:30px"><span class="l1">KANZLEI</span><span class="l2">MERIDIAN</span></div>
  <nav class="nav"><span>Kanzlei</span><span>Rechtsgebiete</span><span>Mandantenbewertungen</span><span>Team</span><span>Räumlichkeiten</span><span>Kontakt</span></nav>
  <div class="nav-cta">Kontakt aufnehmen</div>
  <h1>Rechtliche Beratung<br>mit Klarheit<br>und Weitblick.</h1>
  <p class="lead">Ihre Rechtsanwaltskanzlei in Kempten (Allgäu)<br>für private und gewerbliche Mandanten.</p>
  <div class="btn">Kontakt aufnehmen <svg width="20" height="10" viewBox="0 0 20 10"><path d="M0 5h18M14 1l4 4-4 4" stroke="#1b1c21" fill="none" stroke-width="1.3"/></svg></div>
</header>

<section class="about">
  <div class="eyebrow abs" style="left:61px;top:49px">Über unsere Kanzlei</div>
  <h2 class="abs" style="left:61px;top:83px">Wir verbinden juristische Kompetenz<br>mit persönlichem Engagement.<br>Für Lösungen, die zu Ihnen passen.</h2>
  <div class="rule abs" style="left:61px;top:204px"></div>
  <p class="abs" style="left:61px;top:238px">Als Rechtsanwaltskanzlei in Kempten (Allgäu) beraten wir<br>sowohl Privatpersonen als auch Unternehmen in vielfältigen<br>rechtlichen Angelegenheiten – kompetent, modern<br>und mandantenorientiert.</p>
  <div class="link abs" style="left:61px;top:352px">Mehr über uns <svg viewBox="0 0 20 10"><path d="M0 5h18M14 1l4 4-4 4" stroke="var(--gold)" fill="none" stroke-width="1.3"/></svg></div>
  <div class="photo" role="img" aria-label="Drei Anwälte im Gespräch an einem hellen Besprechungstisch"></div>
</section>

<section class="services">
  <div class="eyebrow">Unsere Rechtsgebiete</div>
  <div class="cards">
    <div class="card">
      <svg class="ic" viewBox="0 0 42 40" fill="none" stroke="var(--gold)" stroke-width="1.4"><circle cx="21" cy="12" r="6"/><circle cx="9" cy="16" r="4.5"/><circle cx="33" cy="16" r="4.5"/><path d="M10 36c0-7 5-12 11-12s11 5 11 12z"/><path d="M2 34c0-5 3-9 8-9M40 34c0-5-3-9-8-9"/></svg>
      <h3>Ausgewählte<br>Mandantenbewertungen</h3>
      <p>Erfahrungen unserer Mandanten sprechen für unsere Arbeit.</p>
      <svg class="arr" viewBox="0 0 20 10"><path d="M0 5h18M14 1l4 4-4 4" stroke="var(--gold)" fill="none" stroke-width="1.3"/></svg>
    </div>
    <div class="card">
      <svg class="ic" viewBox="0 0 42 40" fill="none" stroke="var(--gold)" stroke-width="1.4"><path d="M21 4v30M8 10h26M14 36h14M8 10l-6 13h12zM34 10l-6 13h12z"/><path d="M2 23a6 4 0 0 0 12 0M28 23a6 4 0 0 0 12 0"/></svg>
      <h3>Rechtsgebiete</h3>
      <p>Umfassende Beratung in allen wichtigen Rechtsbereichen.</p>
      <svg class="arr" viewBox="0 0 20 10"><path d="M0 5h18M14 1l4 4-4 4" stroke="var(--gold)" fill="none" stroke-width="1.3"/></svg>
    </div>
    <div class="card">
      <svg class="ic" viewBox="0 0 42 40" fill="none" stroke="var(--gold)" stroke-width="1.4"><rect x="6" y="8" width="24" height="30"/><path d="M12 8V2h24v30h-6M11 16h14M11 22h14M11 28h10"/></svg>
      <h3>Call-to-Action (CTA)</h3>
      <p>Nehmen Sie Kontakt auf –<br>wir sind für Sie da.</p>
      <svg class="arr" viewBox="0 0 20 10"><path d="M0 5h18M14 1l4 4-4 4" stroke="var(--gold)" fill="none" stroke-width="1.3"/></svg>
    </div>
    <div class="card">
      <svg class="ic" viewBox="0 0 42 40" fill="none" stroke="var(--gold)" stroke-width="1.4"><path d="M4 38h34M8 38V12h12v26M20 38V4h14v34M12 18h4M12 24h4M12 30h4M24 10h6M24 16h6M24 22h6M24 28h6"/></svg>
      <h3>Räumlichkeiten</h3>
      <p>Moderne Kanzleiräume<br>für persönliche Gespräche.</p>
      <svg class="arr" viewBox="0 0 20 10"><path d="M0 5h18M14 1l4 4-4 4" stroke="var(--gold)" fill="none" stroke-width="1.3"/></svg>
    </div>
    <div class="card">
      <svg class="ic" viewBox="0 0 42 40" fill="none" stroke="var(--gold)" stroke-width="1.4"><rect x="2" y="4" width="38" height="32"/><circle cx="13" cy="13" r="3.5"/><path d="M2 32l12-11 8 7 7-6 11 10"/></svg>
      <h3>Image-Video</h3>
      <p>Einblicke in unsere Kanzlei –<br>persönlich und authentisch.</p>
      <svg class="arr" viewBox="0 0 20 10"><path d="M0 5h18M14 1l4 4-4 4" stroke="var(--gold)" fill="none" stroke-width="1.3"/></svg>
    </div>
  </div>
</section>

<section class="team">
  <div class="eyebrow abs" style="left:61px;top:42px">Unser Team</div>
  <div class="photo" role="img" aria-label="Gruppenbild des gesamten Kanzleiteams in dunkler Businesskleidung auf hellem Pflaster"></div>
  <h2 class="abs" style="left:763px;top:109px">Gemeinsam für Ihr Recht.<br>Persönlich. Kompetent. Engagiert.</h2>
  <div class="rule abs" style="left:763px;top:200px"></div>
  <p class="abs" style="left:763px;top:228px;font-size:12px;line-height:20px;color:var(--muted)">Unsere Anwälte und Mitarbeiter stehen Ihnen mit<br>Fachwissen und Erfahrung zur Seite. Lernen Sie<br>uns kennen.</p>
  <div class="link abs" style="left:763px;top:326px">Zum Team <svg viewBox="0 0 20 10"><path d="M0 5h18M14 1l4 4-4 4" stroke="var(--gold)" fill="none" stroke-width="1.3"/></svg></div>
</section>

<section class="rooms">
  <div class="photo" role="img" aria-label="Wartebereich mit Holzlamellenwand, schwarzen Ledersofas und großem Bergbild"></div>
  <div class="eyebrow abs" style="left:728px;top:49px;color:#e5e2dc">Räumlichkeiten</div>
  <h2 class="abs" style="left:728px;top:83px">Ein Ort für Vertrauen<br>und gute Gespräche.</h2>
  <div class="rule abs" style="left:728px;top:162px"></div>
  <p class="abs" style="left:728px;top:183px;font-size:12px;line-height:20px;color:#c9c6c0">Unsere modernen Kanzleiräume bieten den passenden<br>Rahmen für persönliche Beratung auf Augenhöhe.</p>
  <div class="link abs" style="left:728px;top:247px;color:var(--gold)">Mehr Eindrücke <svg viewBox="0 0 20 10"><path d="M0 5h18M14 1l4 4-4 4" stroke="var(--gold)" fill="none" stroke-width="1.3"/></svg></div>
</section>

<section class="quotes">
  <div class="eyebrow abs" style="left:61px;top:34px;font-weight:500">Was unsere Mandanten sagen</div>
  <svg class="abs" style="left:61px;top:80px" width="34" height="28" viewBox="0 0 34 28"><path d="M2 28V14C2 6 6 2 14 0v5c-4 1-6 4-6 9h6v14zM20 28V14c0-8 4-12 12-14v5c-4 1-6 4-6 9h6v14z" fill="var(--gold)"/></svg>
  <div class="quote" style="left:124px">„Sehr kompetente Beratung und schnelle<br>Hilfe. Ich fühlte mich jederzeit gut betreut<br>und verstanden.“<br>– M. aus Kempten</div>
  <div class="stars" style="left:124px;top:172px"><svg viewBox="0 0 24 24"><path d="M12 2l3 7 7 .6-5.4 4.7 1.7 7.2L12 17.8 5.7 21.5l1.7-7.2L2 9.6 9 9z"/></svg><svg viewBox="0 0 24 24"><path d="M12 2l3 7 7 .6-5.4 4.7 1.7 7.2L12 17.8 5.7 21.5l1.7-7.2L2 9.6 9 9z"/></svg><svg viewBox="0 0 24 24"><path d="M12 2l3 7 7 .6-5.4 4.7 1.7 7.2L12 17.8 5.7 21.5l1.7-7.2L2 9.6 9 9z"/></svg><svg viewBox="0 0 24 24"><path d="M12 2l3 7 7 .6-5.4 4.7 1.7 7.2L12 17.8 5.7 21.5l1.7-7.2L2 9.6 9 9z"/></svg><svg viewBox="0 0 24 24"><path d="M12 2l3 7 7 .6-5.4 4.7 1.7 7.2L12 17.8 5.7 21.5l1.7-7.2L2 9.6 9 9z"/></svg></div>
  <div class="vsep" style="left:424px"></div>
  <div class="quote" style="left:474px">„Professionell, zuverlässig und menschlich.<br>Eine Kanzlei, der man vertrauen kann.“<br><br>– Unternehmen, Kempten</div>
  <div class="stars" style="left:474px;top:172px"><svg viewBox="0 0 24 24"><path d="M12 2l3 7 7 .6-5.4 4.7 1.7 7.2L12 17.8 5.7 21.5l1.7-7.2L2 9.6 9 9z"/></svg><svg viewBox="0 0 24 24"><path d="M12 2l3 7 7 .6-5.4 4.7 1.7 7.2L12 17.8 5.7 21.5l1.7-7.2L2 9.6 9 9z"/></svg><svg viewBox="0 0 24 24"><path d="M12 2l3 7 7 .6-5.4 4.7 1.7 7.2L12 17.8 5.7 21.5l1.7-7.2L2 9.6 9 9z"/></svg><svg viewBox="0 0 24 24"><path d="M12 2l3 7 7 .6-5.4 4.7 1.7 7.2L12 17.8 5.7 21.5l1.7-7.2L2 9.6 9 9z"/></svg><svg viewBox="0 0 24 24"><path d="M12 2l3 7 7 .6-5.4 4.7 1.7 7.2L12 17.8 5.7 21.5l1.7-7.2L2 9.6 9 9z"/></svg></div>
  <div class="vsep" style="left:775px"></div>
  <div class="quote" style="left:826px">„Die Beratung war klar, verständlich<br>und zielorientiert. Absolute Empfehlung.“<br><br>– J. aus dem Allgäu</div>
  <div class="stars" style="left:826px;top:172px"><svg viewBox="0 0 24 24"><path d="M12 2l3 7 7 .6-5.4 4.7 1.7 7.2L12 17.8 5.7 21.5l1.7-7.2L2 9.6 9 9z"/></svg><svg viewBox="0 0 24 24"><path d="M12 2l3 7 7 .6-5.4 4.7 1.7 7.2L12 17.8 5.7 21.5l1.7-7.2L2 9.6 9 9z"/></svg><svg viewBox="0 0 24 24"><path d="M12 2l3 7 7 .6-5.4 4.7 1.7 7.2L12 17.8 5.7 21.5l1.7-7.2L2 9.6 9 9z"/></svg><svg viewBox="0 0 24 24"><path d="M12 2l3 7 7 .6-5.4 4.7 1.7 7.2L12 17.8 5.7 21.5l1.7-7.2L2 9.6 9 9z"/></svg><svg viewBox="0 0 24 24"><path d="M12 2l3 7 7 .6-5.4 4.7 1.7 7.2L12 17.8 5.7 21.5l1.7-7.2L2 9.6 9 9z"/></svg></div>
</section>

<footer class="contact">
  <h2>Lassen Sie uns über<br>Ihr Anliegen sprechen.</h2>
  <p class="small abs" style="left:474px;top:33px">Wir freuen uns darauf, Sie kennenzulernen und<br>gemeinsam die beste Lösung für Ihr Anliegen zu finden.</p>
  <div class="btn abs" style="left:877px;top:33px;width:198px;height:38px;font-size:13px;color:#fff">Kontakt aufnehmen <svg width="20" height="10" viewBox="0 0 20 10"><path d="M0 5h18M14 1l4 4-4 4" stroke="#fff" fill="none" stroke-width="1.3"/></svg></div>
  <div class="hr"></div>
  <div class="logo abs" style="left:61px;top:130px"><span class="l1" style="font-size:23px">KANZLEI</span><span class="l2" style="font-size:14px">MERIDIAN</span></div>
  <p class="foot abs" style="left:290px;top:125px">Kanzlei Meridian<br>Lindenweg 12<br>87439 Kempten (Allgäu)</p>
  <p class="foot abs" style="left:524px;top:135px">Telefon:&nbsp;&nbsp;&nbsp; 0831 / 555 27 0<br>E-Mail:&nbsp;&nbsp;&nbsp; info@kanzlei-meridian.de</p>
  <p class="foot abs" style="left:877px;top:144px">Impressum</p>
  <p class="foot abs" style="left:997px;top:144px">Datenschutz</p>
</footer>

</body>
</html>
```